New & Improved KIVORA Business Card

I would like a two sided business card one side dedicated to home automation (security camera installation, television & sound bar mounting (hidden wires optional) , sink installation, fireplace mounting, chandelier installation and one side dedicated to all electronic repairs, In ex: plume band repairs, computer, zTab, laptop repairs, Velofon's, Korvex and etc.. Using the colors on this flyer. The phone number &email I want on both sides is (555) 214-3907 & Tech@Kivora.help. SAME COLOR AS THE FLYER ATTACHED.

Target Market(s)

EVERYONE.

Contact Information for Business Card

I would like a two sided business card one side dedicated to home automation (security camera installation, television & sound bar mounting (hidden wires optional) , sink installation, fireplace mounting, chandelier installation and one side dedicated to all electronic repairs, In ex: plume band repairs, computer, zTab, laptop repairs, Velofon's, Korvex and etc.. Using the colors on this flyer. The phone number &email I want on both sides is (555) 214-3907 & Tech@Kivora.help

Requirements
Must have
• -TV MOUNTING
-HOME AUTOMATION
-SECURITY CAMERA INSTALLATION
-ALL ELECTRONIC REPAIRS
- (555) 214-3907
-Tech@Kivora.help
-SAME COLOR AS THE FLYER
Nice to have
• Same colors & concept as the flyer attached below.
Should not have
• DO NOT DO A DIFF COLOR I WANT SAME COLOR AS THE FLYER ATTACHED.

```html
<!DOCTYPE html>
<html lang="en">
<head>
<meta charset="utf-8">
<title>KIVORA Business Card</title>
<link rel="stylesheet" href="https://fonts.googleapis.com/css2?family=Montserrat:wght@400;700&family=Inter:wght@600&display=swap">
<style>
  :root {
    --brand-pink: #ee2890;
    --card-grey: #ababab;
    --stage-light: #f8f8f8;
    --ink-dark: #2a2a2a;
    --ink-contact: #1e1e1e;
    --white: #ffffff;
    --edge: #000000;
  }
  * { margin: 0; padding: 0; box-sizing: border-box; }
  html, body { width: 1200px; height: 801px; overflow: hidden; }
  body {
    position: relative;
    background: linear-gradient(to right, var(--brand-pink) 0 633px, var(--stage-light) 633px 100%);
    font-family: "Montserrat", sans-serif;
  }
  .card {
    position: absolute;
    width: 620px;
    height: 355px;
    background: var(--card-grey);
    box-shadow: 2px 2px 0 var(--edge), 0 0 3px rgba(0,0,0,0.15);
    overflow: hidden;
  }
  .card--front { left: 61px; top: 28px; }
  .card--back { left: 517px; top: 421px; }

  .wordmark {
    position: absolute;
    color: var(--white);
    font-family: "Montserrat", sans-serif;
    font-weight: 700;
    line-height: 1;
    white-space: nowrap;
  }
  .card--front .wordmark {
    left: 257px; top: 264px;
    font-size: 66px;
    letter-spacing: 11px;
  }
  .card--back .wordmark {
    left: 392px; top: 29px;
    font-size: 40px;
    letter-spacing: 6.5px;
  }

  .contact-row {
    position: absolute;
    left: 14px; top: 193px;
    display: flex;
    align-items: center;
    font-size: 18px;
    letter-spacing: 1.6px;
    color: var(--ink-contact);
  }
  .contact-item { display: flex; align-items: center; }
  .contact-item svg { display: block; }
  .contact-item--phone svg { margin-right: 5px; }
  .contact-item--email { margin-left: 17px; }
  .contact-item--email svg { margin-right: 13px; }

  .services-band {
    position: absolute;
    left: 0; right: 0; top: 227px; bottom: 0;
    background: var(--brand-pink);
    border-top: 2px solid var(--white);
  }
  .services-list {
    position: absolute;
    left: 92px;
    width: 436px;
    display: flex;
    justify-content: space-between;
    align-items: center;
    font-family: "Inter", sans-serif;
    font-weight: 600;
    font-size: 15px;
    letter-spacing: 1.5px;
    color: var(--ink-dark);
    white-space: nowrap;
  }
  .services-list--top { top: 38px; }
  .services-list--bottom { top: 72px; }
  .divider {
    display: inline-block;
    width: 3px; height: 14px;
    background: var(--white);
  }
</style>
</head>
<body>
  <section class="card card--front" aria-label="Card front">
    <div class="wordmark">KIVORA</div>
  </section>

  <section class="card card--back" aria-label="Card back">
    <div class="wordmark">KIVORA</div>

    <div class="contact-row">
      <span class="contact-item contact-item--phone">
        <svg width="18" height="20" viewBox="0 0 24 24" aria-hidden="true">
          <path fill="#ee2890" d="M6.6 2.2l2.6 4.3c.3.5.2 1.1-.2 1.5L7.3 9.6c1.2 2.6 3.4 4.8 6 6l1.6-1.7c.4-.4 1-.5 1.5-.2l4.3 2.6c.5.3.7.9.5 1.4l-1 2.6c-.3.7-1 1.1-1.8 1C10 20.6 3.4 14 2.7 5.6c-.1-.8.3-1.5 1-1.8l1.6-.7"/>
        </svg>
        (555) 214-3907
      </span>
      <span class="contact-item contact-item--email">
        <svg width="22" height="16" viewBox="0 0 22 16" aria-hidden="true">
          <rect width="22" height="16" rx="1" fill="#ee2890"/>
          <path d="M1 2l10 7 10-7" fill="none" stroke="#ababab" stroke-width="2"/>
        </svg>
        Tech@Kivora.help
      </span>
    </div>

    <div class="services-band">
      <div class="services-list services-list--top">
        <span>TV MOUNTING</span><span class="divider"></span><span>SECURITY CAMERA INSTALLATION</span>
      </div>
      <div class="services-list services-list--bottom">
        <span>HOME AUTOMATION</span><span class="divider"></span><span>ALL ELECTRONIC REPAIRS</span>
      </div>
    </div>
  </section>
</body>
</html>
```